RQV Wellness Co Business Card for food and Beverage Wizards & Alchemists

One main business card design for a wellness enterprise which represents two brands. We need one primary card design, for two different employees. The only difference between the cards will be the name, title and phone number for each employee, all other design elements will be same.
I've uploaded the logos for each brand. I have also uploaded a mockup which I made using Google's drawing tool. I can provide example images of business cards we find attractive if you would like some help picturing what we like.
I'm picturing the color splash on the back of the card below the two logos to be a dark burgundy or blue. This may sound a bit silly but the feel of the card and color should look almost like wizard dress robes. Dark emerald green, dark blue and dark burgundy with black undertones and gold lace.

Reason: Thank you all for the submissions. I will need some extra time to give you feedback. Cheers

Target Market(s)

Healthy food and beverage industry

Industry/Entity Type

Health And Wellness

Contact Information for Business Card

On one side we would like the business name, location, title of employee, employee name and contact details. On the flip side we would like our two brand logos and a splash of color. We would like the card to have a black font with some gold accents if possible. We would also like the trim of the business card or a middle ply within the card stock to have a color other than white.

Font styles to use
Serif

Colors
ec1f27
0255a3
00a990

Requirements
Must have
• Bold dark colors, happy to provide sample photos of business cards I like from snapgallery. Must have a version for two different employees. Must be sharp, modern and chic.
Nice to have
• Thick card stock layer in between the front and back of card that is either black or gold lace or something to make it feel, well let's say to make it feel expensive.
Should not have
• Should not have any cartoon-ey elements. All business.

```html
<!DOCTYPE html>
<html lang="en">
<head>
<meta charset="utf-8">
<title>RQV Wellness Co – Business Card</title>
<link rel="stylesheet" href="https://fonts.googleapis.com/css2?family=Source+Sans+3:wght@400;600;700&display=swap">
<style>
  :root {
    --stage: #555555;
    --card-front: #000000;
    --card-back: #0b0b0b;
    --ink: #f0f0f0;
    --gold: #e8b000;
    --robe-deep: #0a0c2e;
    --robe-wine: #5e0a22;
  }
  * { margin: 0; padding: 0; box-sizing: border-box; }
  html, body { width: 1200px; height: 900px; overflow: hidden; }
  body {
    background: var(--stage);
    font-family: "Source Sans 3", sans-serif;
    color: var(--ink);
    position: relative;
  }
  .card {
    position: absolute;
    top: 170px;
    width: 347px;
    height: 561px;
    overflow: hidden;
  }
  .card--front { left: 259px; background: var(--card-front); text-align: center; }
  .card--back { left: 631px; background: var(--card-back); }

  .company { position: absolute; top: 67px; width: 100%; }
  .company__name { font-size: 23px; font-weight: 700; line-height: 30px; }
  .company__location { font-size: 19px; line-height: 24px; }

  .person { position: absolute; top: 332px; width: 100%; }
  .person__name { font-size: 25px; font-weight: 700; color: var(--gold); line-height: 32px; }
  .person__title { font-size: 19px; line-height: 26px; }

  .contact { position: absolute; top: 421px; width: 100%; }
  .contact__icons { display: flex; justify-content: center; gap: 5px; height: 26px; margin-bottom: 12px; }
  .contact__line { font-size: 19px; line-height: 25px; }

  .brand-mark {
    position: absolute;
    left: 0; width: 100%;
    text-align: center;
    font-weight: 700;
    color: var(--ink);
  }
  .brand-mark--primary { top: 54px; font-size: 34px; letter-spacing: 2px; }
  .brand-mark--secondary { top: 196px; font-size: 22px; }
  .brand-mark__dot {
    display: block;
    width: 12px; height: 12px;
    margin: 10px auto 0;
    border-radius: 50%;
    background: var(--ink);
  }
  .robe-band { position: absolute; inset: 0; }
</style>
</head>
<body>
  <section class="card card--front">
    <div class="company">
      <p class="company__name">RQV Wellness Co</p>
      <p class="company__location">Larkspur Vale,CA</p>
    </div>
    <div class="person">
      <p class="person__name">Marcus Hale</p>
      <p class="person__title">Beverage Alchemist</p>
    </div>
    <div class="contact">
      <div class="contact__icons">
        <svg width="26" height="26" viewBox="0 0 26 26" aria-label="Phone">
          <circle cx="13" cy="13" r="13" fill="var(--gold)"/>
          <path d="M9.2 7.5c.5-.4 1.1-.3 1.4.2l1.2 2c.3.5.2 1-.2 1.3l-.8.6c.6 1.4 1.6 2.5 3 3.2l.6-.8c.3-.4.9-.5 1.3-.2l2 1.2c.5.3.6.9.2 1.4l-.9 1c-.6.6-1.5.8-2.3.5-3.1-1.2-5.4-3.5-6.5-6.6-.3-.8-.1-1.7.5-2.3z" fill="#000"/>
        </svg>
        <svg width="26" height="26" viewBox="0 0 26 26" aria-label="Email">
          <circle cx="13" cy="13" r="13" fill="var(--gold)"/>
          <rect x="7.5" y="9" width="11" height="8" fill="#000"/>
          <path d="M7.8 9.3 13 13.5l5.2-4.2" fill="none" stroke="var(--gold)" stroke-width="1"/>
        </svg>
      </div>
      <p class="contact__line">415.555.0148</p>
      <p class="contact__line">rqvwellnessco@mail.com</p>
    </div>
  </section>

  <section class="card card--back">
    <div class="brand-mark brand-mark--primary">RQV</div>
    <div class="brand-mark brand-mark--secondary">Elixir Guild<span class="brand-mark__dot"></span></div>
    <svg class="robe-band" width="347" height="561" viewBox="0 0 347 561">
      <defs>
        <linearGradient id="robe-fade" x1="0" y1="0" x2="0.4" y2="1">
          <stop offset="0" stop-color="var(--robe-deep)"/>
          <stop offset="1" stop-color="var(--robe-wine)"/>
        </linearGradient>
      </defs>
      <polygon points="0,460 347,260 347,561 0,561" fill="url(#robe-fade)"/>
      <line x1="0" y1="460" x2="347" y2="260" stroke="var(--gold)" stroke-width="3"/>
      <line x1="0" y1="472" x2="347" y2="272" stroke="var(--gold)" stroke-width="1"/>
    </svg>
  </section>
</body>
</html>
```